We need letterhead, Business Cards, and envelops designed. We have attached a design of our logo and a sample of letterhead idea that was started but never perfected, it is only an idea for the letterhead if you can design something better we may love that also we are open to change.
We want a design that looks professional in style. we are a non profit trade association in the construction industry. the green color in the attached design represent green building, and we like that. also if you just want to enhance the letterhead sample that we attached that would be fine also.
Thanks and good luck
also the name that should show on the first business cards should be Morgan Feltwick, Director are web address is www.pvtrn.org

```html
<!DOCTYPE html>
<html lang="en">
<head>
<meta charset="utf-8">
<title>PVTRN Letterhead</title>
<link rel="stylesheet" href="https://fonts.googleapis.com/css2?family=Open+Sans:wght@400;600&family=Didact+Gothic&display=swap">
<style>
  :root {
    --ink: #000000;
    --text: #3a3a3a;
    --green: #3d7a1e;
    --paper: #ffffff;
  }
  * { margin: 0; padding: 0; box-sizing: border-box; }
  html, body { width: 927px; height: 1200px; overflow: hidden; background: var(--paper); }
  .letterhead { position: relative; width: 927px; height: 1200px; background: var(--paper); }

  .brand { position: absolute; left: 67px; top: 62px; }
  .brand-name {
    display: flex; align-items: center; gap: 14px;
    font-family: "Open Sans", sans-serif; font-weight: 400;
    font-size: 86px; line-height: 1; letter-spacing: 2px; color: var(--ink);
  }
  .brand-mark { width: 22px; height: 22px; background: var(--green); }
  .brand-full {
    margin-top: 8px;
    font-family: "Open Sans", sans-serif; font-weight: 400;
    font-size: 13px; color: var(--text); letter-spacing: 0.3px;
  }

  .contact {
    position: absolute; top: 106px;
    font-family: "Didact Gothic", sans-serif;
    font-size: 13px; line-height: 19px; letter-spacing: 2.2px; color: var(--text);
  }
  .contact-address { left: 509px; }
  .contact-lines { left: 690px; }
  .contact-line { display: flex; align-items: center; height: 19px; }
  .contact-icon { width: 12px; height: 12px; margin-right: 26px; }
</style>
</head>
<body>
<main class="letterhead">
  <header>
    <div class="brand">
      <div class="brand-name"><span>PVTRN</span><span class="brand-mark"></span></div>
      <p class="brand-full">Pacific Valley Trades Roundtable Network</p>
    </div>

    <address class="contact contact-address" style="font-style:normal">
      address<br>
      4321 first street<br>
      anytown, State ZIP
    </address>

    <div class="contact contact-lines">
      <div class="contact-line">
        <svg class="contact-icon" viewBox="0 0 12 12" aria-label="Phone">
          <path d="M1 4 Q6 0 11 4 L9.5 5.5 L8 4.5 L4 4.5 L2.5 5.5 Z" fill="var(--green)"/>
          <rect x="3" y="6" width="6" height="4.5" rx="1" fill="var(--green)"/>
        </svg>
        <span>123-456-7890</span>
      </div>
      <div class="contact-line">
        <svg class="contact-icon" viewBox="0 0 12 12" aria-label="Fax">
          <rect x="3" y="1" width="6" height="3" fill="none" stroke="var(--green)" stroke-width="1.2"/>
          <rect x="1" y="4" width="10" height="5" rx="1" fill="none" stroke="var(--green)" stroke-width="1.2"/>
          <rect x="3" y="7.5" width="6" height="3.5" fill="var(--paper)" stroke="var(--green)" stroke-width="1.2"/>
        </svg>
        <span>123-456-7891</span>
      </div>
      <div class="contact-line">
        <svg class="contact-icon" viewBox="0 0 12 12" aria-label="Web">
          <circle cx="6" cy="6" r="5" fill="none" stroke="var(--green)" stroke-width="1.2"/>
          <ellipse cx="6" cy="6" rx="2.2" ry="5" fill="none" stroke="var(--green)" stroke-width="1"/>
          <line x1="1" y1="6" x2="11" y2="6" stroke="var(--green)" stroke-width="1"/>
        </svg>
        <span>www.pvtrn.org</span>
      </div>
    </div>
  </header>
</main>
</body>
</html>
```